Velorin Wine Label For Canopy Haven

Lantern Brook Winery is in need of a wine label for new wine being release. This wine will be used as a fundraiser for Canopy Haven, a chimpanzee santuary in Georgia. The label should reflect a high-end, classy image and the label should suggest the chimp philanthropy without specifically naming the organization (for legal purposes). The label can be a little whimsical without being too cartoonish or child like. This wine will be sold for $30 so it should project a sense of elegance too.
Updates

holiday season makes it difficult to get feedback necessary for approval. just need a few more days...

Industry/Entity Type

Winery

Font styles to use
Sans Serif

Requirements
Must have
• Label should show common design appearance as other labels downloaded.
• Label should be a dark (emerald) green color. Label should have wine name "Velorin" in center. Label should include an image or silhouette of a chimp on it
Should not have
• no cartoonish images;

```html
<!DOCTYPE html>
<html lang="en">
<head>
<meta charset="utf-8">
<title>Velorin Wine Label</title>
<link href="https://fonts.googleapis.com/css2?family=Cormorant+Garamond:wght@600&display=swap" rel="stylesheet">
<style>
  :root {
    --paper: #ffffff;
    --emerald: #0a6a35;
    --emerald-deep: #0b4a30;
    --gold: #b08a10;
  }
  html, body {
    margin: 0;
    padding: 0;
    width: 1200px;
    height: 1000px;
    overflow: hidden;
    background: var(--paper);
  }
  .label {
    display: block;
    width: 1200px;
    height: 1000px;
  }
  .label-band { fill: url(#emeraldGlow); }
  .gold-rule { fill: none; stroke: var(--gold); }
  .gold-fill { fill: var(--gold); }
  .wine-name {
    font-family: "Cormorant Garamond", Georgia, serif;
    font-weight: 600;
    font-size: 86px;
    fill: var(--gold);
  }
</style>
</head>
<body>
<svg class="label" viewBox="0 0 1200 1000" xmlns="http://www.w3.org/2000/svg">
  <defs>
    <radialGradient id="emeraldGlow" cx="50%" cy="50%" r="60%">
      <stop offset="0%" stop-color="#0a6a35"/>
      <stop offset="55%" stop-color="#0a6a35"/>
      <stop offset="100%" stop-color="#0b4a30"/>
    </radialGradient>
  </defs>

  <!-- label body with pointed crest -->
  <path class="label-band" d="M10 185 H520 L600 77 L680 185 H1190 V815 H680 L600 922 L520 815 H10 Z"/>

  <!-- outer gold border lines -->
  <polyline class="gold-rule" stroke-width="7" points="10,204 527,204 600,105 673,204 1190,204"/>
  <polyline class="gold-rule" stroke-width="7" points="10,797 527,797 600,895 673,797 1190,797"/>

  <!-- side verticals -->
  <line class="gold-rule" stroke-width="3" x1="363" y1="207" x2="363" y2="795"/>
  <line class="gold-rule" stroke-width="3" x1="836" y1="207" x2="836" y2="795"/>

  <!-- central crest frame -->
  <path class="gold-rule" stroke-width="7" d="M380 223 H514 L600 109 L686 223 H820 V776 H686 L600 891 L514 776 H380 Z"/>

  <!-- arched ground lines -->
  <path class="gold-rule" stroke-width="4" d="M384 393 Q600 347 816 393"/>
  <path class="gold-rule" stroke-width="2" d="M384 407 Q600 353 816 407"/>

  <!-- emblem area -->
  <rect class="gold-fill" x="540" y="260" width="140" height="104" rx="18"
        role="img" aria-label="Space for the label emblem"/>

  <!-- wine name -->
  <circle class="gold-fill" cx="403" cy="500" r="7"/>
  <text class="wine-name" x="427" y="528" textLength="347" lengthAdjust="spacingAndGlyphs">VELORIN</text>
  <circle class="gold-fill" cx="797" cy="500" r="7"/>

  <!-- lower divider rules -->
  <line class="gold-rule" stroke-width="2" x1="384" y1="608" x2="816" y2="608"/>
  <line class="gold-rule" stroke-width="6" x1="384" y1="619" x2="816" y2="619"/>
</svg>
</body>
</html>
```